The Linen Loft Co

We need a business card design for our wardrobe company.
Please visit our website www.gentlelinenlofts.com to get an idea of who we are.

```html
<!DOCTYPE html>
<html lang="en">
<head>
<meta charset="utf-8">
<title>The Linen Loft Co – Business Card</title>
<link rel="stylesheet" href="https://fonts.googleapis.com/css2?family=Roboto:wght@400;500;700&display=swap">
<style>
  :root {
    --page-bg: #e9e6e2;
    --card-bg: #ffffff;
    --ink: #000000;
    --text-dark: #111111;
    --text-body: #3a3a3a;
    --text-muted: #a6a6a6;
  }
  * { margin: 0; padding: 0; box-sizing: border-box; }
  html, body {
    width: 1200px; height: 989px; overflow: hidden;
    background: var(--page-bg);
    font-family: "Roboto", Arial, sans-serif;
  }
  .card {
    position: absolute; left: 80px; top: 196px;
    width: 1040px; height: 598px;
    background: var(--card-bg);
    overflow: hidden;
    box-shadow: 0 6px 18px rgba(0,0,0,0.18);
  }
  .card__swoosh { position: absolute; inset: 0; width: 100%; height: 100%; }
  .brand { position: absolute; left: 485px; top: 72px; display: flex; align-items: center; gap: 16px; }
  .brand__mark { width: 86px; height: 86px; border: 4px solid var(--ink); }
  .brand__text { text-align: center; }
  .brand__name { font-size: 28px; font-weight: 500; color: var(--text-dark); letter-spacing: 0.2px; text-transform: uppercase; white-space: nowrap; }
  .brand__tagline { font-size: 23px; font-weight: 500; color: var(--text-dark); margin-top: 10px; white-space: nowrap; }
  .contact { position: absolute; left: 59px; top: 292px; }
  .contact__name { font-size: 38px; font-weight: 700; color: var(--text-dark); line-height: 1.1; }
  .contact__role { font-size: 26px; font-weight: 500; color: var(--text-muted); line-height: 1.1; margin-top: 2px; }
  .contact__details { font-size: 25px; color: var(--text-body); line-height: 31px; margin-top: 14px; }
  .contact__address { margin-bottom: 10px; }
</style>
</head>
<body>
  <div class="card">
    <svg class="card__swoosh" viewBox="0 0 1105 636" preserveAspectRatio="none" aria-hidden="true">
      <path d="M0 0 H540 C330 25 110 110 0 265 Z" fill="var(--ink)"/>
      <path d="M8 190 C140 90 300 30 465 2 L495 2 C320 35 150 100 8 190 Z" fill="var(--card-bg)"/>
      <path d="M1105 636 H590 C800 612 1000 530 1105 415 Z" fill="var(--ink)"/>
      <path d="M1100 445 C990 530 810 600 640 634 L612 636 C800 605 980 535 1100 445 Z" fill="var(--card-bg)"/>
    </svg>

    <div class="brand">
      <div class="brand__mark"></div>
      <div class="brand__text">
        <div class="brand__name">The Linen Loft Co</div>
        <div class="brand__tagline">Storage Made to Measure</div>
      </div>
    </div>

    <div class="contact">
      <div class="contact__name">Daniel Hart</div>
      <div class="contact__role">President</div>
      <div class="contact__details">
        <div class="contact__address">
          <p>Unit 4, 22 Harrow Lane,</p>
          <p>London N7 8QR</p>
        </div>
        <p>P. 020 7946 0215</p>
        <p>info@gentlelinenlofts.com</p>
        <p>www.gentlelinenlofts.com</p>
      </div>
    </div>
  </div>
</body>
</html>
```